Upmarket Dessert Lounge needs a Business Card Design

We are an upmarket dessert lounge needing a business card to match our image.

We want something that is simple yet beautiful, feminine, classy, sophisticated and elegant. We want it to stand out and don't mind if it is bold.

The design should include our logo and colours of red or maroon with gold highlights. We don't mind if black is used.

Marlow & Quince

Target Market(s)

For those who like to indulge or treat themselves and give in to their temptations on good quality desserts.

Industry/Entity Type

Business

Requirements
Must have
• Must include our logo and our name

Marlow & Quince

M & Q

```html
<!DOCTYPE html>
<html lang="en">
<head>
<meta charset="utf-8">
<title>Marlow &amp; Quince – Business Card</title>
<link rel="stylesheet" href="https://fonts.googleapis.com/css2?family=Open+Sans:wght@400;600;700&display=swap">
<style>
  :root {
    --maroon: #7a1416;
    --gold: #fdd29a;
    --white: #ffffff;
    --ink: #333333;
    --backdrop: #d9d9d9;
  }
  * { margin: 0; padding: 0; box-sizing: border-box; }
  html, body { width: 956px; height: 1200px; overflow: hidden; }
  body {
    background: var(--backdrop);
    font-family: "Open Sans", Arial, sans-serif;
    position: relative;
  }
  .card {
    position: absolute;
    width: 797px;
    height: 454px;
    border-radius: 26px;
    overflow: hidden;
  }
  .card-front { left: 83px; top: 95px; background: var(--white); }
  .card-back { left: 75px; top: 635px; background: var(--gold); }

  .front-wave { position: absolute; left: 0; top: 0; width: 797px; height: 454px; }

  .brand-name {
    position: absolute;
    left: 40px;
    top: 152px;
    width: 390px;
    text-align: center;
    font-size: 36px;
    font-weight: 600;
    color: var(--maroon);
    letter-spacing: 1px;
  }

  .contact { position: absolute; left: 470px; top: 78px; color: var(--ink); }
  .contact-name { font-size: 21px; font-weight: 700; line-height: 26px; }
  .contact-role { font-size: 21px; font-weight: 400; line-height: 26px; letter-spacing: 0.5px; }
  .contact-list { list-style: none; margin-top: 20px; font-size: 18.5px; line-height: 30px; }
  .contact-list .gap { margin-top: 4px; }
  .contact-list b { font-weight: 700; }

  .address {
    position: absolute;
    left: 440px;
    top: 386px;
    width: 340px;
    text-align: center;
    color: var(--white);
    font-size: 17.5px;
    line-height: 27px;
  }

  .monogram {
    position: absolute;
    left: 0; top: 0;
    width: 797px; height: 454px;
    display: flex;
    align-items: center;
    justify-content: center;
    font-size: 120px;
    font-weight: 400;
    color: var(--maroon);
  }
</style>
</head>
<body>
  <section class="card card-front">
    <svg class="front-wave" viewBox="0 0 797 454" aria-hidden="true">
      <path fill="var(--gold)" d="M0,398 C180,428 330,420 460,368 C590,318 710,312 797,334 L797,454 L0,454 Z"/>
      <path fill="var(--maroon)" d="M0,412 C180,442 330,434 470,382 C600,334 715,330 797,352 L797,454 L0,454 Z"/>
      <path fill="none" stroke="var(--gold)" stroke-width="10" d="M412,396 C520,352 650,334 797,366"/>
    </svg>

    <div class="brand-name">Marlow &amp; Quince</div>

    <div class="contact">
      <div class="contact-name">Your Name</div>
      <div class="contact-role">Designation</div>
      <ul class="contact-list">
        <li><b>p</b> : 123-456-7890</li>
        <li><b>c</b> : 123-456-7890</li>
        <li><b>f</b> : 123-456-7890</li>
        <li class="gap"><b>e</b> : name@yourwebsite.com</li>
        <li><b>w</b> : www.marlowandquince.com</li>
      </ul>
    </div>

    <div class="address">0000, Street Name<br>City Name, Country Code.</div>
  </section>

  <section class="card card-back">
    <div class="monogram">M &amp; Q</div>
  </section>
</body>
</html>
```